Doctor to Patient Management Website

I need a design for a health management website that connects doctors to patients. The website will consist of: A main page mainly describing our goal, services, and initiatives towards (Who we are AKA "About Us", Our services, Contact Us, Quick Links for health tips, Language selection, Find a doctor, search bar, Member Login Section, small glossary section below with links to all entities mentioned prior, Help section (Helpful tips and tutorials, Used to request help from admin, customer service, to resolve issues or get assistance). A profile page with two types:1) Doctor Profile: Doctor Personal info (First, Last, Middle Name, Title), Clinic, Hospital Info, Department, Credentials, Years of Experience, Patients rating, #Patients seen during the current week, #Patients seen in total, Picture, Link to email doctor, Link to print doctor's profile). Tabs for "About Me", "Contact Info", "Ratings & Comments", "Documents" (To be downloaded and uploaded by patient), "Patients (List of Patients alphabetical order by name)", "Calendar" (to see doctor's availability for booking) underneath all links. 2) Patient profile: About me, Personal Info, Height, Weight, Blood Type, Age, DOB, Name, etc..., Message and email link.Picture of patient with menu made of "Personal Data", "Biometrics", "Allergies", "Illnesses", "Medications", "Medical Procedures", "Doctors" treating the patient, "Documents" (To be downloaded and uploaded by patient). Underneath all, other patients he or she is related to (For example: family member, so patient can't connect to other patients who are family members)3) Login section: New Users will have option to register using:First Name (Required), Last Name, Middle (not required), Address (Not required), City (Required), Country (Required), Email (Not required), Phone Number (Required), Choose UserName, Password, Account Type (Doctor or Patient). Once registered, they will log in using UserName, Password, and Account_Type.Curent Users will log in using UserName, Password, and Account_Type and option to retrieve username or password.Pages to include (Login Page - Registration Page - Retrieve Username and Reset Password Page)Please see link below:https://plumcrate-adwerks.net/importance-claiming-vantorix-quibble-zarn/Pictures are attached to this project as an inspirationFYI: Dummy text can be used to fill in the business, services, and descriptive information. Feel free to include your own ideas in the layout, design, categories, patterns, and more to and showcase your talent. Design and pictures provided are available as source of ideas.

Target Market(s)

Age: 21+ / Family Oriented / Medical Sector / Metropolitan Area / Educated and non Educated Users

Industry/Entity Type

Health Care

Number of Pages Required

5+ page

Font styles to use
Sans Serif

Colors

Designer to choose colors to be used in the design.

Requirements
Must have
• Thin layer design
• Simple font - No serif
• Clean menu with light but solid colors (No Gradient effect)
Nice to have
• Different color themes (2 or 3) can be combined
• Sample pictures for illustration (either as an ad or to go with the flow of your design)
• Dashboard Feel (Suggested but not required)
Should not have
• Artistic fonts - with Serif
• Dark color themes

```html
<!DOCTYPE html>
<html lang="en">
<head>
<meta charset="utf-8">
<title>Medora — Find a doctor</title>
<link rel="stylesheet" href="https://fonts.googleapis.com/css2?family=Montserrat:wght@400;500;600;700;800&family=Open+Sans:wght@400;600&display=swap">
<style>
:root{
  --blue:#1a7fe8;
  --blue-text:#1b7fe3;
  --navy:#1e2640;
  --ink:#333a44;
  --muted:#555c66;
  --pale-1:#ebf5fe;
  --pale-2:#e0edf9;
  --help-bg:#e3eef9;
  --white:#ffffff;
  --line:#c9ced6;
  --foot-text:#b7bdcc;
}
*{box-sizing:border-box;margin:0;padding:0}
html,body{width:1200px;height:3197px;overflow:hidden}
body{font-family:"Open Sans",Arial,sans-serif;color:var(--ink);background:var(--white);position:relative}
a{color:inherit;text-decoration:none}
.section-title{font-family:"Montserrat",Arial,sans-serif;font-weight:500;color:var(--blue-text);font-size:34px;text-align:center}
.btn-dark{display:inline-flex;align-items:center;justify-content:center;background:var(--navy);color:var(--white);font-family:"Montserrat",Arial,sans-serif;font-size:15px;font-weight:500;border-radius:3px}

/* header */
.site-header{position:absolute;left:0;top:0;width:1200px;height:81px;background:var(--blue)}
.brand{position:absolute;left:143px;top:17px;font-family:"Montserrat",Arial,sans-serif;font-weight:800;font-size:36px;color:var(--white);letter-spacing:.5px}
.main-nav{position:absolute;left:343px;top:0;height:81px;width:460px;display:flex;align-items:center;justify-content:space-between;font-family:"Montserrat",Arial,sans-serif;font-size:12.5px;color:var(--white);white-space:nowrap}
.lang-select{position:absolute;left:825px;top:21px;width:109px;height:39px;border:1px solid rgba(255,255,255,.8);border-radius:3px;display:flex;align-items:center;gap:7px;padding-left:11px;color:var(--white);font-size:13px;font-family:"Montserrat",Arial,sans-serif}
.flag{width:18px;height:12px;background:#c8102e;border:2px solid #ffffff;outline:1px solid #233f8c}
.member-login{position:absolute;left:944px;top:21px;width:111px;height:39px;background:var(--white);color:#1e2640;border-radius:3px;font-family:"Montserrat",Arial,sans-serif;font-size:13px;font-weight:500;display:flex;align-items:center;justify-content:center}

/* hero */
.hero{position:absolute;left:0;top:81px;width:1200px;height:533px;overflow:hidden}
.hero-photo{position:absolute;inset:0;background:linear-gradient(100deg,#c8c3b9 0%,#8f8b84 30%,#55575b 55%,#9fa3a8 80%,#d8d9db 100%)}
.hero-shade{position:absolute;inset:0;background:rgba(20,28,40,.35)}
.hero-title{position:absolute;left:0;width:1200px;top:200px;text-align:center;font-family:"Montserrat",Arial,sans-serif;font-weight:600;font-size:50px;color:var(--white)}
.search-bar{position:absolute;left:360px;top:264px;width:478px;height:55px;background:var(--white);border-radius:3px;display:flex;align-items:center}
.search-bar span{flex:1;padding-left:24px;font-size:15px;color:#6a6f77}
.search-btn{width:46px;height:45px;margin-right:5px;background:var(--navy);border-radius:3px;display:flex;align-items:center;justify-content:center}
.slide-arrow{position:absolute;top:247px;width:36px;height:36px;border-radius:50%;background:var(--white);display:flex;align-items:center;justify-content:center}
.slide-arrow.prev{left:44px}
.slide-arrow.next{left:1118px}

/* welcome */
.welcome{position:absolute;left:0;top:614px;width:1200px;height:339px;text-align:center}
.welcome .section-title{position:absolute;top:72px;width:1200px}
.welcome p{position:absolute;left:145px;top:120px;width:910px;font-size:14.8px;line-height:25.5px;color:var(--ink)}
.welcome .btn-dark{position:absolute;left:539px;top:211px;width:122px;height:47px}

/* services */
.services{position:absolute;left:0;top:953px;width:1200px;height:490px;display:flex}
.services .half{width:600px;height:490px}
.services .half.left{background:var(--pale-1)}
.services .half.right{background:var(--pale-2)}
.services .section-title{position:absolute;top:70px;width:1200px}
.service-card{position:absolute;top:138px;width:440px;text-align:center}
.service-card.one{left:137px}
.service-card.two{left:622px}
.service-icon{width:100px;height:102px;margin:0 auto;border-radius:8px;background:linear-gradient(180deg,#cfe3f8,#b9d6f3)}
.service-card h3{margin-top:22px;font-family:"Montserrat",Arial,sans-serif;font-weight:500;font-size:26px;color:var(--blue-text)}
.service-card p{margin-top:8px;font-size:11.3px;line-height:20.5px;color:var(--muted)}
.btn-outline{display:inline-flex;align-items:center;justify-content:center;width:120px;height:47px;margin-top:17px;border:1px solid #3a3f48;border-radius:3px;font-family:"Montserrat",Arial,sans-serif;font-size:12px;color:var(--ink)}

/* health tips */
.health-tips{position:absolute;left:0;top:1443px;width:1200px;height:573px}
.health-tips .section-title{position:absolute;top:72px;width:1200px}
.tip{position:absolute;top:138px;width:298px}
.tip.t1{left:144px}.tip.t2{left:450px}.tip.t3{left:757px}
.tip-photo{width:298px;height:224px}
.tip.t1 .tip-photo{background:linear-gradient(180deg,#ece6e0,#dcd3c8 70%,#e8924a 100%)}
.tip.t2 .tip-photo{background:radial-gradient(circle at 50% 50%,#3a4550,#1d2630 75%)}
.tip.t3 .tip-photo{background:linear-gradient(180deg,#9db7cf 0%,#6f90ad 50%,#4d7ea6 100%)}
.tip-kicker{margin-top:12px;font-size:16px;color:var(--ink)}
.tip-link{margin-top:6px;font-size:17.5px;color:var(--blue-text);font-family:"Montserrat",Arial,sans-serif}
.health-tips .btn-dark{position:absolute;left:539px;top:445px;width:122px;height:49px}

/* help */
.help{position:absolute;left:0;top:2016px;width:1200px;height:362px;background:var(--help-bg)}
.help .section-title{position:absolute;top:74px;width:1200px}
.help-card{position:absolute;top:134px;width:216px;height:145px;background:var(--white);text-align:center;padding-top:26px}
.help-card.h1{left:145px}.help-card.h2{left:377px}.help-card.h3{left:607px}.help-card.h4{left:839px}
.help-card svg{display:block;margin:0 auto;height:36px}
.help-card p{margin:18px auto 0;width:160px;font-size:14.8px;line-height:20px;color:var(--ink)}

/* contact */
.contact{position:absolute;left:0;top:2378px;width:1200px;height:465px}
.contact .section-title{position:absolute;top:70px;width:1200px}
.field{position:absolute;height:43px;border:1px solid var(--line);font-size:13px;color:#8a8f96;padding:12px 14px}
.field.name{left:215px;top:130px;width:241px}
.field.phone{left:480px;top:130px;width:240px}
.field.email{left:744px;top:130px;width:241px}
.field.message{left:215px;top:198px;width:770px;height:116px}
.contact .btn-dark{position:absolute;left:552px;top:337px;width:96px;height:47px}

/* footer */
.site-footer{position:absolute;left:0;top:2843px;width:1200px;height:354px;background:var(--navy);color:var(--white)}
.foot-head{position:absolute;top:52px;font-family:"Montserrat",Arial,sans-serif;font-size:19px;font-weight:500}
.foot-list{position:absolute;top:90px;list-style:none;font-size:12.5px;color:var(--foot-text);line-height:27.2px}
.newsletter{position:absolute;left:678px;top:96px;width:219px;height:41px;background:#dde2ea;display:flex;align-items:center;justify-content:space-between;padding:0 12px 0 16px;font-size:12px;color:#3a3f48}
.social{position:absolute;left:936px;top:92px;display:flex;gap:30px}
.social span{width:20px;height:20px;border-radius:50%;background:var(--foot-text)}
.foot-rule{position:absolute;left:145px;top:278px;width:910px;height:1px;background:#4a526b}
.copyright{position:absolute;top:306px;width:1200px;text-align:center;font-size:12px;color:var(--white)}
</style>
</head>
<body>

<header class="site-header">
  <a class="brand" href="#">Medora</a>
  <nav class="main-nav">
    <a href="#">Home</a><a href="#">About Us</a><a href="#">Services</a><a href="#">Find a Doctor</a><a href="#">Contact Us</a><a href="#">Help</a>
  </nav>
  <div class="lang-select"><span class="flag"></span>English
    <svg width="10" height="7" viewBox="0 0 10 7"><path d="M1 1l4 4 4-4" stroke="#fff" stroke-width="1.5" fill="none"/></svg>
  </div>
  <a class="member-login" href="#">Member Login</a>
</header>

<section class="hero">
  <div class="hero-photo" role="img" aria-label="Doctor at a desk on a video call with a patient on a laptop"></div>
  <div class="hero-shade"></div>
  <h1 class="hero-title">Find a doctor</h1>
  <div class="search-bar"><span>Category, Name, Area or Zipcode</span>
    <div class="search-btn"><svg width="18" height="18" viewBox="0 0 18 18"><circle cx="7.5" cy="7.5" r="5.5" stroke="#fff" stroke-width="2.4" fill="none"/><path d="M11.5 11.5l5 5" stroke="#fff" stroke-width="2.6" stroke-linecap="round"/></svg></div>
  </div>
  <div class="slide-arrow prev"><svg width="12" height="14" viewBox="0 0 12 14"><path d="M9 1L3 7l6 6" stroke="#1e2640" stroke-width="2.6" fill="none"/></svg></div>
  <div class="slide-arrow next"><svg width="12" height="14" viewBox="0 0 12 14"><path d="M3 1l6 6-6 6" stroke="#1e2640" stroke-width="2.6" fill="none"/></svg></div>
</section>

<section class="welcome">
  <h2 class="section-title">Welcome to Medora</h2>
  <p>Maecenas vel tortor accumsan quam varius imperdiet eget elit. Aenean facilisis tincidunt lectus, dictum nisi luctus eget. Vivamus efficitur ex condimentum, malesuada eros eget, feugiat nibh. Sed tellus ex, imperdiet eget gravida sit amet, volutpat eget turpis. In nec ultricies est. Etiam mattis augue vehicula odio posuere, sit amet tempus lectus luctus.</p>
  <a class="btn-dark" href="#">Learn More</a>
</section>

<section class="services">
  <div class="half left"></div><div class="half right"></div>
  <h2 class="section-title">Services</h2>
  <article class="service-card one">
    <div class="service-icon" role="img" aria-label="Line icon of a doctor with stethoscope"></div>
    <h3>Donec amet</h3>
    <p>Nam et tortor in ante iaculis porttitor in luctus mi. Vivamus gravida sem a pretium euismod. Nam lobortis, purus et fringilla tempus, risus eros dignissim diam, eget finibus sem risus sit amet eros</p>
    <a class="btn-outline" href="#">Learn More</a>
  </article>
  <article class="service-card two">
    <div class="service-icon" role="img" aria-label="Line icon of a nurse"></div>
    <h3>Phasellus blandit</h3>
    <p>Nam et tortor in ante iaculis porttitor in luctus mi. Vivamus gravida sem a pretium euismod. Nam lobortis, purus et fringilla tempus, risus eros dignissim diam, eget finibus sem risus sit amet eros</p>
    <a class="btn-outline" href="#">Learn More</a>
  </article>
</section>

<section class="health-tips">
  <h2 class="section-title">Health Tips</h2>
  <article class="tip t1"><div class="tip-photo" role="img" aria-label="Woman meditating on a yoga mat"></div><p class="tip-kicker">Aliquam erat volutpat</p><p class="tip-link">Cras augue magna placerat</p></article>
  <article class="tip t2"><div class="tip-photo" role="img" aria-label="Fresh vegetables and spices on a dark table"></div><p class="tip-kicker">Etiam quis aliquet</p><p class="tip-link">Phasellus nisl est condimentum</p></article>
  <article class="tip t3"><div class="tip-photo" role="img" aria-label="Runner jogging beside the sea"></div><p class="tip-kicker">Aenean sed quam</p><p class="tip-link">Nunc sit amet consequa</p></article>
  <a class="btn-dark" href="#">View All</a>
</section>

<section class="help">
  <h2 class="section-title">Help</h2>
  <div class="help-card h1">
    <svg viewBox="0 0 36 36" width="36"><circle cx="18" cy="18" r="17" fill="#1b7fe3"/><circle cx="18" cy="10" r="2.6" fill="#fff"/><rect x="15.5" y="15" width="5" height="13" rx="1" fill="#fff"/></svg>
    <p>Helpful tips and tutorials</p>
  </div>
  <div class="help-card h2">
    <svg viewBox="0 0 40 36" width="40"><path d="M20 2L38 34H2z" fill="#1b7fe3" stroke="#1b7fe3" stroke-width="2" stroke-linejoin="round"/><rect x="18" y="12" width="4" height="12" rx="1" fill="#fff"/><circle cx="20" cy="28.5" r="2.2" fill="#fff"/></svg>
    <p>Used to request help from admin</p>
  </div>
  <div class="help-card h3">
    <svg viewBox="0 0 40 36" width="40"><path d="M6 24v-6a14 14 0 0128 0v6" stroke="#1b7fe3" stroke-width="4" fill="none"/><rect x="3" y="20" width="8" height="13" rx="3" fill="#1b7fe3"/><rect x="29" y="20" width="8" height="13" rx="3" fill="#1b7fe3"/></svg>
    <p>Customer Service</p>
  </div>
  <div class="help-card h4">
    <svg viewBox="0 0 46 34" width="46"><rect x="1" y="1" width="44" height="32" rx="3" fill="#1b7fe3"/><path d="M3 4l20 15L43 4" stroke="#fff" stroke-width="2.6" fill="none"/></svg>
    <p>To resolve issues or get assistance</p>
  </div>
</section>

<section class="contact">
  <h2 class="section-title">Contact Us</h2>
  <div class="field name">Name</div>
  <div class="field phone">Phone</div>
  <div class="field email">Email</div>
  <div class="field message">Message</div>
  <a class="btn-dark" href="#">Submit</a>
</section>

<footer class="site-footer">
  <h4 class="foot-head" style="left:145px">Links</h4>
  <ul class="foot-list" style="left:145px"><li>Home</li><li>About Us</li><li>Services</li><li>Find a Doctor</li><li>Contact Us</li></ul>
  <ul class="foot-list" style="left:241px"><li>Help</li><li>Member Login</li><li>Select Language</li><li>Register</li></ul>
  <h4 class="foot-head" style="left:405px">Glossary</h4>
  <ul class="foot-list" style="left:405px"><li>Donec vestibulum</li><li>Quisque aliquet</li><li>Pellentesque</li><li>Etiam id</li><li>Vivamus lacus</li></ul>
  <ul class="foot-list" style="left:533px"><li>Fusce vitae</li><li>Aenean placerat</li><li>Vestibulum ante</li><li>Vestibulum eget</li><li>Phasellus</li></ul>
  <h4 class="foot-head" style="left:678px">Newsletter Signup</h4>
  <div class="newsletter">Email Address
    <svg width="20" height="16" viewBox="0 0 20 16"><rect x="1" y="2" width="18" height="13" rx="1.5" fill="#1e2640"/><path d="M2 3.5l8 6 8-6" stroke="#dde2ea" stroke-width="1.5" fill="none"/></svg>
  </div>
  <h4 class="foot-head" style="left:938px">Follow us on</h4>
  <div class="social"><span></span><span></span><span></span></div>
  <div class="foot-rule"></div>
  <p class="copyright">Copyright © 2019 Medora. All rights reserved.</p>
</footer>

</body>
</html>
```